Business card design for my company.
I would like the card's background colour to be black. You can also see our web site to get an idea of our brand. https://www.tmwhomecrafting.com.au/
- Name
- Email

```html
<!DOCTYPE html>
<html lang="en">
<head>
<meta charset="utf-8">
<title>TMW Home Crafting – Business Card</title>
<link rel="stylesheet" href="https://fonts.googleapis.com/css2?family=Montserrat:wght@400;500;700;800&display=swap">
<style>
  :root {
    --backdrop: #4a4a4a;
    --card: #141414;
    --green: #0f9447;
    --white: #f3f3f3;
    --text: #e6e6e6;
  }
  * { box-sizing: border-box; margin: 0; padding: 0; }
  html, body {
    width: 1200px; height: 800px; overflow: hidden;
    background: var(--backdrop);
    font-family: "Montserrat", sans-serif;
  }
  .canvas { position: relative; width: 1200px; height: 800px; }

  .card {
    position: absolute;
    background: var(--card);
    border-radius: 26px;
    border: 3px solid var(--green);
    box-shadow: 0 18px 36px rgba(0,0,0,.35);
    color: var(--text);
  }

  /* Portrait back: contact side */
  .card-back {
    left: 150px; top: 120px; width: 320px; height: 560px;
    display: flex; flex-direction: column; align-items: center;
    padding: 60px 28px 40px;
    text-align: center;
  }
  .brand {
    display: flex; align-items: center; gap: 12px;
    color: var(--white);
    font-weight: 800;
    text-transform: uppercase;
    letter-spacing: 2px;
    line-height: 1.15;
  }
  .brand-square { background: var(--green); flex: none; }
  .card-back .brand { font-size: 24px; text-align: left; }
  .card-back .brand-square { width: 22px; height: 22px; }

  .person { margin-top: 78px; }
  .person-name { color: var(--green); font-weight: 800; font-size: 28px; }
  .person-role { margin-top: 4px; font-size: 15px; font-weight: 500; color: var(--text); }

  .icon-row {
    margin-top: 24px; width: 100%;
    display: flex; align-items: center; gap: 8px;
  }
  .rule { flex: 1; height: 1.5px; background: var(--green); }
  .icon {
    width: 26px; height: 26px; border-radius: 7px;
    background: var(--green);
    display: flex; align-items: center; justify-content: center;
  }
  .icon svg { width: 16px; height: 16px; }

  .contact-list {
    list-style: none; margin-top: 18px;
    font-size: 13.5px; line-height: 1.75; font-weight: 400;
  }
  .divider { width: 100%; height: 1.5px; background: var(--green); margin-top: 22px; }
  .address { margin-top: 16px; font-size: 14px; }

  /* Landscape front: brand side */
  .card-front {
    left: 540px; top: 240px; width: 560px; height: 320px;
    display: flex; align-items: center; justify-content: center;
  }
  .card-front .brand { font-size: 40px; gap: 20px; }
  .card-front .brand-square { width: 34px; height: 34px; }
</style>
</head>
<body>
<main class="canvas">

  <section class="card card-back" aria-label="Business card, contact side">
    <div class="brand">
      <span class="brand-square"></span>
      <span>TMW Home<br>Crafting</span>
    </div>

    <div class="person">
      <h1 class="person-name">Liam Carter</h1>
      <p class="person-role">General Manager</p>
    </div>

    <div class="icon-row">
      <span class="rule"></span>
      <span class="icon" aria-label="Phone">
        <svg viewBox="0 0 16 16"><path d="M4 2l2 3-1.3 1.3a8 8 0 0 0 5 5L11 10l3 2-1 2.5C7 14 2 9 1.5 3z" fill="#fff"/></svg>
      </span>
      <span class="icon" aria-label="Email">
        <svg viewBox="0 0 16 16"><rect x="2" y="4" width="12" height="8" fill="none" stroke="#fff" stroke-width="1.5"/><path d="M2 4l6 5 6-5" fill="none" stroke="#fff" stroke-width="1.5"/></svg>
      </span>
      <span class="icon" aria-label="Website">
        <svg viewBox="0 0 16 16"><circle cx="8" cy="8" r="6" fill="none" stroke="#fff" stroke-width="1.5"/><path d="M2 8h12M8 2c-3 3-3 9 0 12M8 2c3 3 3 9 0 12" fill="none" stroke="#fff" stroke-width="1.2"/></svg>
      </span>
      <span class="rule"></span>
    </div>

    <ul class="contact-list">
      <li>0400 123 456</li>
      <li>info@tmwhomecrafting.com.au</li>
      <li>www.tmwhomecrafting.com.au</li>
    </ul>

    <div class="divider"></div>
    <p class="address">Eastvale, Tasmania, Australia</p>
  </section>

  <section class="card card-front" aria-label="Business card, brand side">
    <div class="brand">
      <span class="brand-square"></span>
      <span>TMW Home<br>Crafting</span>
    </div>
  </section>

</main>
</body>
</html>
```